New business card for a regional office of a US M&A company

We need business card for a finance company, office based in Hong Kong , our Head office is in US, our business is to Merge and acquires companies , the new office will be a regional office for the Asia Pacific region. We want to use the head office logo as attached ( but don't have to be exactly the same, can be a variation to it) as a base and then add Asia Pacific alongside the logo.
We would prefer to have be bilingual Eng + Chinese, although we don't really have Chinese company name .

Industry/Entity Type

Business

Contact Information for Business Card

Clara Jo Tsang
 

VP,
APAC M&A Operations
Orin Vantage Asia Pacific Limited
 
Unit 1407, K18
18 Tai Lok Shan Road, 
Hong Kong 
 
M: +852 6038 1742
T : +852 2836 4100
F : +852 2836 4177
VOIP: 4158
 
cjtsang@orinvantage.com

Font styles to use
Serif
Sans Serif

Colors

Designer to choose colors to be used in the design.

Requirements
Must have
• APAC Office

```html
<!DOCTYPE html>
<html lang="en">
<head>
<meta charset="utf-8">
<title>Orin Vantage – Business Card</title>
<link rel="stylesheet" href="https://fonts.googleapis.com/css2?family=Open+Sans:wght@400;600;700;800&display=swap">
<style>
  :root {
    --stage: #1c1c1e;
    --paper: #ffffff;
    --paper-shade: #eef0f2;
    --teal: #1fa9c8;
    --rule-blue: #2c6db3;
    --navy: #0f2a47;
    --navy-deep: #0b1f36;
    --ink: #14263f;
    --grey: #555b63;
    --white: #ffffff;
  }
  * { box-sizing: border-box; margin: 0; padding: 0; }
  html, body {
    width: 1200px; height: 963px; overflow: hidden;
    background: var(--stage);
    font-family: "Open Sans", Arial, sans-serif;
  }
  .canvas {
    position: relative; width: 1200px; height: 963px;
    display: flex; flex-direction: column; align-items: center;
    justify-content: center; gap: 55px;
  }
  .card {
    position: relative; width: 700px; height: 400px;
    border-radius: 18px; overflow: hidden;
  }

  /* Front */
  .card--front {
    background: linear-gradient(135deg, var(--paper-shade) 0%, var(--paper) 45%, var(--paper) 100%);
  }
  .front__wordmark {
    position: absolute; left: 42px; top: 34px;
    font-weight: 800; font-size: 46px; letter-spacing: 1px;
    color: var(--teal); text-transform: uppercase; white-space: nowrap;
  }
  .front__rule {
    position: absolute; left: 118px; top: 150px;
    width: 360px; height: 2px; background: var(--rule-blue);
  }
  .contact-list {
    position: absolute; left: 42px; top: 168px;
    list-style: none; font-size: 13.5px; line-height: 21px; color: var(--grey);
  }
  .contact-list li { display: flex; align-items: center; gap: 8px; white-space: nowrap; }
  .contact-list svg { width: 12px; height: 12px; fill: var(--teal); flex: none; }
  .person {
    position: absolute; right: 42px; top: 210px; text-align: right;
  }
  .person__name {
    font-weight: 700; font-size: 21px; letter-spacing: 1px;
    color: var(--ink); text-transform: uppercase; white-space: nowrap;
  }
  .person__role { font-size: 14px; color: var(--ink); margin-top: 2px; white-space: nowrap; }
  .person__address {
    margin-top: 18px; font-size: 14px; line-height: 20px; color: var(--grey);
  }
  .front__bands { position: absolute; inset: 0; width: 100%; height: 100%; }
  .front__voip {
    position: absolute; right: 42px; bottom: 7px;
    font-size: 13px; color: var(--white); letter-spacing: 0.5px;
  }

  /* Back */
  .card--back {
    background: radial-gradient(ellipse at 50% 40%, #1b3d63 0%, var(--navy) 55%, var(--navy-deep) 100%);
  }
  .back__map {
    position: absolute; left: 50px; top: 40px; width: 600px; height: 320px;
    border-radius: 45%;
    background: radial-gradient(ellipse at center, rgba(80,120,165,0.26) 0%, rgba(80,120,165,0.08) 60%, rgba(80,120,165,0) 75%);
  }
  .back__brand {
    position: absolute; inset: 0;
    display: flex; flex-direction: column; align-items: center; justify-content: center; gap: 22px;
  }
  .back__square {
    width: 62px; height: 62px; border: 7px solid var(--white);
  }
  .back__name {
    font-weight: 800; font-size: 52px; letter-spacing: 3px;
    color: var(--white); text-transform: uppercase; white-space: nowrap;
  }
</style>
</head>
<body>
<main class="canvas">

  <section class="card card--front" aria-label="Card front">
    <div class="front__wordmark">Orin Vantage</div>
    <div class="front__rule"></div>

    <ul class="contact-list">
      <li><svg viewBox="0 0 12 12"><rect x="3" y="0.5" width="6" height="11" rx="1.2"/></svg>+852 6038 1742</li>
      <li><svg viewBox="0 0 12 12"><path d="M2.5 0.8 L4.6 3.4 L3.6 4.8 C4.4 6.6 5.6 7.8 7.2 8.5 L8.6 7.4 L11.2 9.5 L9.8 11.2 C5 11 1 7 0.8 2.2 Z"/></svg>+852 2836 4100</li>
      <li><svg viewBox="0 0 12 12"><rect x="3" y="0.5" width="6" height="4"/><rect x="0.5" y="4" width="11" height="5" rx="1"/><rect x="3" y="8" width="6" height="3.5"/></svg>+852 2836 4177</li>
      <li><svg viewBox="0 0 12 12"><path d="M0.5 2 H11.5 V10 H0.5 Z M0.5 2 L6 6.5 L11.5 2"/></svg>cjtsang@orinvantage.com</li>
    </ul>

    <div class="person">
      <div class="person__name">Clara Jo Tsang</div>
      <div class="person__role">VP, APAC M&amp;A Operations</div>
      <div class="person__address">Unit 1407, K18 18 Tai Lok<br>Shan Road, Hong Kong</div>
    </div>

    <svg class="front__bands" viewBox="0 0 700 400" preserveAspectRatio="none" aria-hidden="true">
      <path d="M0,300 C220,310 480,340 700,372 L700,380 C480,352 230,326 0,318 Z" fill="var(--teal)"/>
      <path d="M0,318 C230,326 480,352 700,380 L700,400 L0,400 Z" fill="var(--navy)"/>
    </svg>
    <div class="front__voip">VOIP: 4158</div>
  </section>

  <section class="card card--back" aria-label="Card back">
    <div class="back__map" role="img" aria-label="Faint dotted world map"></div>
    <div class="back__brand">
      <div class="back__square"></div>
      <div class="back__name">Orin Vantage</div>
    </div>
  </section>

</main>
</body>
</html>
```